Business Cards Design for the electrical wholesaler: clean bold dynamic :)

We need a business card design that would follow our latest brand guidelines. As an electrical wholesaler we want to bring a fresh look and feel into the industry. The design should be clean bold and dynamic. It should come alive with the renewed energy of our green colour. Our grey colour should keep things balanced and complement the notion of maturity and responsibility. We employ Lato as a corporate font however are not bound by this font and we’re open to interpretation here.

Target Market(s)

Electrical contractors

Industry/Entity Type

Business

Contact Information for Business Card

Logo
Name & Surname: Halyna Dorosh
Job Title: Director of Marketing
Email: halya.dorosh@quillmail.example
Cell phone: XXX.XXX.XXXX
Address: 20517 - 87 Ave. Edmonton, AB, Canada. T6K 4N8
Business Phone: 780.555.0184
Website: www.brovix.example

Font styles to use
Other font styles liked:
• Lato

Requirements
Must have
• Logo & website
Nice to have
• Brand elements - some of them you may find in the attached Brand Guidelines (e.g. three lines on the background signifying "W")

```html
<!DOCTYPE html>
<html lang="en">
<head>
<meta charset="utf-8">
<title>Brovix business cards</title>
<link href="https://fonts.googleapis.com/css2?family=Work+Sans:wght@400;500&display=swap" rel="stylesheet">
<style>
  :root {
    --green: #7dc242;
    --grey: #4d4d4f;
    --text: #3a3a3a;
    --stage: #1b1b1b;
    --card-front: #ffffff;
    --card-back-a: #1f1f1f;
    --card-back-b: #333331;
  }
  * { margin: 0; padding: 0; box-sizing: border-box; }
  html, body {
    width: 1200px; height: 897px; overflow: hidden;
    background: var(--stage);
    font-family: "Work Sans", sans-serif;
  }
  .canvas { position: relative; width: 1200px; height: 897px; }
  .card {
    position: absolute; left: 303px; width: 595px; height: 338px;
    border-radius: 20px; overflow: hidden;
  }
  .card--front { top: 92px; background: var(--card-front); }
  .card--back {
    top: 469px;
    background: linear-gradient(150deg, var(--card-back-a) 45%, var(--card-back-b) 100%);
  }
  .brand {
    position: absolute; display: flex; align-items: center;
    font-weight: 500; letter-spacing: -0.5px;
  }
  .brand__mark { display: block; background: var(--green); }
  .card--front .brand { left: 43px; top: 138px; gap: 12px; color: var(--grey); font-size: 46px; }
  .card--front .brand__mark { width: 30px; height: 30px; }
  .card--back .brand { left: 112px; top: 120px; gap: 18px; color: #fff; font-size: 72px; }
  .card--back .brand__mark { width: 46px; height: 46px; }
  .divider {
    position: absolute; left: 312px; top: 94px; width: 2px; height: 151px;
    background: var(--green);
  }
  .details { position: absolute; left: 343px; top: 94px; color: var(--text); }
  .details__name { color: var(--green); font-size: 24px; font-weight: 500; line-height: 28px; }
  .details__title { font-size: 15px; line-height: 18px; margin-bottom: 10px; }
  .details__address { font-size: 15px; line-height: 18.5px; margin-bottom: 9px; letter-spacing: 0.3px; }
  .contact { list-style: none; font-size: 15px; line-height: 19px; letter-spacing: 0.3px; }
  .contact li { display: flex; align-items: center; }
  .contact svg { width: 9px; height: 9px; margin-right: 11px; flex: none; }
  .contact .accent { color: var(--green); }
</style>
</head>
<body>
<main class="canvas">
  <section class="card card--front" aria-label="Business card front">
    <div class="brand"><span class="brand__mark"></span><span>brovix</span></div>
    <div class="divider"></div>
    <div class="details">
      <p class="details__name">Halyna Dorosh</p>
      <p class="details__title">Founder</p>
      <p class="details__address">20517 87ave<br>T6K4N8 Edmonton, Alberta</p>
      <ul class="contact">
        <li>
          <svg viewBox="0 0 10 10" aria-hidden="true"><path d="M2 0.5 L3.6 0.5 L4 3 L3 3.6 Q3.8 5.8 6.2 7 L6.8 6 L9.4 6.4 L9.4 8 Q9.4 9.5 8 9.5 Q1 8.5 0.5 2 Q0.5 0.5 2 0.5Z" fill="var(--green)"/></svg>
          <span>780.555.0184</span>
        </li>
        <li>
          <svg viewBox="0 0 10 10" aria-hidden="true"><rect x="0.7" y="2" width="8.6" height="6" fill="none" stroke="var(--green)" stroke-width="1.2"/><path d="M0.7 2 L5 5.4 L9.3 2" fill="none" stroke="var(--green)" stroke-width="1.2"/></svg>
          <span>hello@brovix.example</span>
        </li>
        <li>
          <svg viewBox="0 0 10 10" aria-hidden="true"><g fill="none" stroke="var(--green)" stroke-width="0.9"><circle cx="5" cy="5" r="4.3"/><ellipse cx="5" cy="5" rx="1.8" ry="4.3"/><path d="M0.7 5 H9.3 M1.5 2.8 H8.5 M1.5 7.2 H8.5"/></g></svg>
          <span>www.<span class="accent">brovix</span>.example</span>
        </li>
      </ul>
    </div>
  </section>

  <section class="card card--back" aria-label="Business card back">
    <div class="brand"><span class="brand__mark"></span><span>brovix</span></div>
  </section>
</main>
</body>
</html>
```